Business card for a Exhibition booth fabrication company

Hi. My company would like to change our corporate name card. We are an events and Exhibition stand builder company. We would like our corporate name card to resonate what we do. I need someone to create something unique that relates to the industry that I am in. The graphic designer should be creative to incorporate the elements of my industry and try to blend in well in the design of the card. Our aim is to ensure that we are unique and our card can look different from our competitors.
Updates

Target Market(s)

Marketing and events manager from all companies

Contact Information for Business Card

The business card should have the following details:
Name
Job Title
Email
Website

Colors

Designer to choose colors to be used in the design.

Requirements
Must have
• The card must be look something that is relevant to the service that I am providing. My website is: www.velmora-buildworks.com
• You can see my website to get more information on what service that I am doing
Nice to have
• On the back of my card, I would like to have a globe image with the incorporation of my company logo. This is to indicate that my services can be done in any part of the world.

```html
<!DOCTYPE html>
<html lang="en">
<head>
<meta charset="utf-8">
<title>Velmora Buildworks – Business Card</title>
<link rel="stylesheet" href="https://fonts.googleapis.com/css2?family=Arimo:wght@400;700&family=Montserrat:wght@600&family=Open+Sans:wght@400&display=swap">
<style>
  :root {
    --stage-light: #dcdddf;
    --stage-dark: #a6a7a9;
    --card-white: #ffffff;
    --brand-red: #e31e25;
    --slate: #636466;
    --slate-map: #7d7e80;
    --ink-grey: #6d6e71;
    --silver: #c9cacc;
    --text-light: #ffffff;
  }
  * { margin: 0; padding: 0; box-sizing: border-box; }
  html, body { width: 1200px; height: 1117px; overflow: hidden; }
  body {
    position: relative;
    background: linear-gradient(90deg, var(--stage-light) 0%, #bfc0c2 55%, var(--stage-dark) 100%);
    font-family: "Open Sans", Arial, sans-serif;
  }
  .card {
    position: absolute;
    left: 223px;
    width: 754px;
    height: 431px;
    border-radius: 34px;
    overflow: hidden;
  }
  .card--front { top: 77px; background: var(--card-white); }
  .card--back { top: 578px; background: var(--slate); }

  /* front */
  .brand-mark {
    position: absolute;
    left: 357px; top: 62px;
    width: 40px; height: 40px;
    background: var(--brand-red);
  }
  .brand-name {
    position: absolute;
    left: 0; right: 0; top: 131px;
    text-align: center;
    font-family: "Montserrat", Arial, sans-serif;
    font-weight: 600;
    font-size: 27px;
    line-height: 34px;
    letter-spacing: 2px;
    color: var(--ink-grey);
  }
  .holder {
    position: absolute;
    left: 0; right: 0; top: 229px;
    text-align: center;
    font-family: "Arimo", Arial, sans-serif;
    font-size: 20px;
    line-height: 30px;
    color: var(--ink-grey);
  }
  .holder__name {
    font-weight: 700;
    font-size: 25px;
    color: var(--brand-red);
  }
  .band { position: absolute; left: 0; top: 0; width: 754px; height: 431px; }
  .contact {
    position: absolute;
    left: 0; right: 0;
    color: var(--text-light);
    font-size: 17px;
    text-align: center;
    display: flex;
    justify-content: center;
    align-items: center;
    gap: 18px;
  }
  .contact__item { display: inline-flex; align-items: center; gap: 8px; }
  .contact__icon { width: 18px; height: 18px; fill: var(--text-light); }
  .contact__icon--globe { fill: none; stroke: var(--text-light); stroke-width: 1.6; }
  .contact--phone { top: 314px; }
  .contact--web { top: 345px; }
  .contact--address { top: 383px; }

  /* back */
  .world-map {
    position: absolute;
    left: 0; top: 67px;
    width: 754px; height: 292px;
    background: radial-gradient(ellipse at 50% 45%, var(--slate-map) 0%, #747577 55%, var(--slate) 100%);
  }
  .back-name {
    position: absolute;
    left: 0; right: 0; top: 188px;
    text-align: center;
    font-family: "Montserrat", Arial, sans-serif;
    font-weight: 600;
    font-size: 40px;
    letter-spacing: 3px;
    color: var(--silver);
  }
  .back-url {
    position: absolute;
    left: 0; right: 0; top: 391px;
    text-align: center;
    font-size: 20px;
    letter-spacing: 5px;
    color: var(--text-light);
  }
</style>
</head>
<body>
  <section class="card card--front">
    <div class="brand-mark"></div>
    <div class="brand-name">VELMORA BUILDWORKS</div>
    <div class="holder"><span class="holder__name">DANIEL HARWICK,</span> PRESIDENT</div>

    <svg class="band" viewBox="0 0 754 431" aria-hidden="true">
      <path d="M0,336 Q377,214 754,336" fill="none" stroke="var(--brand-red)" stroke-width="3"/>
      <path d="M0,347 Q377,233 754,347 L754,431 L0,431 Z" fill="var(--slate)"/>
    </svg>

    <div class="contact contact--phone">
      <span class="contact__item">
        <svg class="contact__icon" viewBox="0 0 24 24"><path d="M6.6 10.8a15.1 15.1 0 0 0 6.6 6.6l2.2-2.2a1 1 0 0 1 1-.25 11.4 11.4 0 0 0 3.6.57 1 1 0 0 1 1 1V20a1 1 0 0 1-1 1A17 17 0 0 1 3 4a1 1 0 0 1 1-1h3.5a1 1 0 0 1 1 1c0 1.25.2 2.45.57 3.57a1 1 0 0 1-.25 1z"/></svg>
        012-345-6789
      </span>
    </div>
    <div class="contact contact--web">
      <span class="contact__item">
        <svg class="contact__icon" viewBox="0 0 24 24"><path d="M2 5h20v14H2z M4 7v.4l8 5.6 8-5.6V7z" fill-rule="evenodd"/></svg>
        info@velmora-buildworks.com
      </span>
      <span class="contact__item">
        <svg class="contact__icon contact__icon--globe" viewBox="0 0 24 24"><circle cx="12" cy="12" r="9"/><ellipse cx="12" cy="12" rx="4" ry="9"/><path d="M3 12h18M5 7h14M5 17h14"/></svg>
        www.velmora-buildworks.com
      </span>
    </div>
    <div class="contact contact--address">Street Name, City Name, Zipcode - 01234</div>
  </section>

  <section class="card card--back">
    <div class="world-map" role="img" aria-label="Faint world map spanning the card, showing global reach"></div>
    <div class="back-name">VELMORA BUILDWORKS</div>
    <div class="back-url">www.velmora-buildworks.com</div>
  </section>
</body>
</html>
```